Corvanth Veylor - Advanced Skincare and undetectable Makeup for Men

We are in need of a professional webpage for our company Corvanth Veylor. We help every man feel his best by looking his best. Inspired by the myth of Corvanth, we offer makeup and skincare products along with education upon their use. Our mission is to celebrate masculinity in all of its forms, regardless of age, race, sexual orientation, or assigned gender at birth.

The webpage would serve as our online store, as a place where our clients can learn about our brand, view our "How-to" video tutorials, and get product information. An online blog will also be hosted in order to keep clients up to date with news, updates, media mentions, etc.

The color schemes that we use are mostly Black and Gold, with Red accents. please keep in mind that this is a men's cosmetics line, and therefore should read powerful, sexy, confident and bold - all with a high end look and feel.

Think along the lines of brands like Lem Brisko, QDV, Belluti, etc.

our logo is included in the files attached. images and copy will be added in at a later time; hence, general images that fit the feel and filler text is encouraged.

The products to be sold include:
a face cleanser in a pump dispenser bottle (1 size)
a mask in a round jar container (1 size)
a moisturizer in a pump container 1 size)
a concealer in a click pen with a brush applicator (3 shades)
a liquid liner pen (4 shades)
a contouring palette (2 shade options)
a setting spray (single option)

Target Market(s)

Millennial Men

Industry/Entity Type

Beauty

Number of Pages Required

5+ page

Font styles to use
Serif

Colors
ec1f27
000000
faa54b

Requirements
Must have
• ur essential requirements are:
• 1) a stunning and engaging landing page that truly captures the ideals of sexuality, boldness and confidence.
• 2) an interactive and engaging online store that is easy to update / add product / information to.
• 3) Product pages supporting various toggling images of the product, a shade selection option, ingredient information, usage instructions, pricing, and a link to a "how to video" unique to each individual product.
• 4) dedicated space where all of the tutorials can be organized together
• 5) an organized Blog section, that would include a segment for a Q&A section for us to update as the brand grows, ongoing contests (that would be easily hidden if there are no contests running at the moment) as well as general news and updates segment.
• 6) an "about us" page, where our customers are able to learn about our story, inspirations, humanitarian efforts and philosophies in product contents and purity.
• 7) a contact us page, which would include social media links, contact email and telephone number as well as physical address to be updated upon launch.
• 8) discrete privacy policy, terms of use, and return policy links available at the bottom of every page
Nice to have
• 1) A posting forum where clients could post their looks using our products, or maybe a live stream of our Pictoval account.
• 2) a member sign in page so that we can collect and store customer information for faster check out, keep track of purchases attached to their email address (future loyalty program plans) and maintain an email database for email notifications and the such.

```html
<!DOCTYPE html>
<html lang="en">
<head>
<meta charset="utf-8">
<title>Contact Us – Corvanth Veylor</title>
<link href="https://fonts.googleapis.com/css2?family=Cinzel:wght@500&family=Montserrat:wght@400;500;600;700&family=Lato:wght@400&family=Ubuntu:wght@400;500&display=swap" rel="stylesheet">
<style>
:root{
  --black:#000;
  --gold:#ad7c36;
  --gold-light:#c8903f;
  --red:#cc0a0f;
  --ink:#111;
  --footer:#272727;
  --footer-bottom:#1e1e1e;
  --footer-text:#c9c9c9;
  --white:#fff;
}
*{box-sizing:border-box;margin:0;padding:0}
html,body{width:1200px;height:1167px;overflow:hidden;background:var(--black)}
body{position:relative;font-family:'Lato',sans-serif;color:var(--white)}
.abs{position:absolute}

/* header */
.site-header{position:absolute;left:0;top:0;width:1200px;height:143px;background:var(--black)}
.brand{position:absolute;left:70px;top:40px;display:flex;flex-direction:column;align-items:center;width:188px}
.brand-mark{width:46px;height:46px;background:var(--gold)}
.brand-name{margin-top:14px;font-family:'Cinzel',serif;font-weight:500;font-size:14px;letter-spacing:6px;color:var(--gold);white-space:nowrap}
.main-nav a{position:absolute;top:62px;font-family:'Lato',sans-serif;font-size:12.5px;color:var(--white);text-decoration:none;white-space:nowrap}
.main-nav a.active{color:var(--gold-light)}
.search{position:absolute;left:1006px;top:60px;font-size:12.5px;display:flex;align-items:center;gap:5px}
.cart{position:absolute;left:1088px;top:54px}
.cart-badge{position:absolute;left:1111px;top:46px;width:19px;height:19px;border-radius:50%;background:#e3101b;color:#fff;font-size:12px;text-align:center;line-height:19px;font-family:'Montserrat',sans-serif}

/* contact band */
.contact-band{position:absolute;left:0;top:143px;width:1200px;height:658px;background:var(--gold)}
.page-title{position:absolute;left:0;width:1200px;top:217px;text-align:center;font-family:'Montserrat',sans-serif;font-weight:500;font-size:34px;color:var(--ink);letter-spacing:.5px}
.page-intro{position:absolute;left:320px;width:490px;top:270px;text-align:center;font-family:'Montserrat',sans-serif;font-size:13px;line-height:21.5px;color:var(--ink)}
.field{position:absolute;border:1px solid #5a3f15;font-size:12.5px;color:#1a1208;padding-left:16px;display:flex;align-items:center}
.field.message{align-items:flex-start;padding-top:16px;padding-left:21px;color:#3a2a10}
.send-btn{position:absolute;left:153px;top:531px;width:501px;height:47px;background:var(--red);color:#fff;font-family:'Montserrat',sans-serif;font-weight:500;font-size:17px;display:flex;align-items:center;justify-content:center;letter-spacing:.3px}
.info{position:absolute;font-family:'Montserrat',sans-serif;font-size:13px;line-height:21.5px;color:var(--ink)}
.info.thin{font-family:'Lato',sans-serif;font-size:13.5px;color:#2a1d0b}
.map{position:absolute;left:682px;top:368px;width:385px;height:325px;background:linear-gradient(135deg,#e9e6df 0%,#dfe2d6 55%,#cfe3c5 100%)}

/* footer */
.site-footer{position:absolute;left:0;top:801px;width:1200px;height:316px;background:var(--footer)}
.footer-heading{position:absolute;top:849px;font-family:'Montserrat',sans-serif;font-weight:700;font-size:13.5px;letter-spacing:.6px;color:#f0f0f0}
.footer-list{position:absolute;list-style:none;font-family:'Ubuntu',sans-serif;font-size:13px;color:var(--footer-text)}
.footer-list li{height:22.6px}
.social{position:absolute;top:887px;width:30px;height:30px;border:1.5px solid #bdbdbd;border-radius:50%;color:#cfcfcf;font-family:'Ubuntu',sans-serif;font-size:12px;display:flex;align-items:center;justify-content:center}
.copyright{position:absolute;left:107px;top:1052px;font-family:'Ubuntu',sans-serif;font-size:13px;color:var(--footer-text)}
.to-top{position:absolute;left:1120px;top:1037px;width:42px;height:42px;border-radius:50%;background:#c9893f}
.footer-bottom{position:absolute;left:0;top:1117px;width:1200px;height:50px;background:var(--footer-bottom)}
.currency{position:absolute;left:109px;top:1134px;font-family:'Ubuntu',sans-serif;font-size:12px;color:#ccc}
.divider{position:absolute;left:170px;top:1130px;width:1px;height:22px;background:#666}
.payments{position:absolute;left:192px;top:1135px;display:flex;gap:12px;font-family:'Ubuntu',sans-serif;font-weight:500;font-size:10.5px;color:#bbb}
</style>
</head>
<body>

<header class="site-header">
  <div class="brand">
    <div class="brand-mark"></div>
    <div class="brand-name">CORVANTH VEYLOR</div>
  </div>
  <nav class="main-nav">
    <a style="left:437px">HOME</a>
    <a style="left:491px">ABOUT US</a>
    <a style="left:574px">PRODUCT</a>
    <a style="left:657px">STORE</a>
    <a style="left:730px">BLOG</a>
    <a class="active" style="left:798px">CONTACT US</a>
    <a style="left:893px">MEMBER LOGIN</a>
  </nav>
  <div class="search">Search
    <svg width="20" height="20" viewBox="0 0 20 20"><circle cx="8" cy="8" r="6.5" fill="none" stroke="#bbb" stroke-width="1.8"/><line x1="13" y1="13" x2="19" y2="19" stroke="#bbb" stroke-width="2"/></svg>
  </div>
  <svg class="cart" width="28" height="28" viewBox="0 0 28 28"><path d="M1 3h4l3 14h15l3-10H7" fill="none" stroke="#fff" stroke-width="1.8"/><path d="M9 10h15M10 13.5h13M12 7v10M16 7v10M20 7v10" stroke="#fff" stroke-width="1"/><circle cx="10" cy="22" r="2.2" fill="none" stroke="#fff" stroke-width="1.6"/><circle cx="21" cy="22" r="2.2" fill="none" stroke="#fff" stroke-width="1.6"/></svg>
  <div class="cart-badge">0</div>
</header>

<main class="contact-band"></main>
<h1 class="page-title">CONTACT US</h1>
<p class="page-intro">Discover the wide range of Halveth available at Groomhall now.Save 20% on Rook &amp; Birch this week at Groomhall.</p>

<div class="field" style="left:157px;top:367px;width:248px;height:40px">First Name</div>
<div class="field" style="left:157px;top:418px;width:247px;height:40px">Last Name</div>
<div class="field" style="left:156px;top:470px;width:248px;height:40px">Email Address</div>
<div class="field message" style="left:411px;top:367px;width:247px;height:143px">Message</div>
<div class="send-btn">SEND MESSAGE</div>

<svg class="abs" style="left:155px;top:606px" width="11" height="14" viewBox="0 0 11 14"><path d="M5.5 0A5 5 0 0 0 .5 5c0 3.5 5 9 5 9s5-5.5 5-9a5 5 0 0 0-5-5z" fill="#111"/><circle cx="5.5" cy="5" r="1.8" fill="#ad7c36"/></svg>
<div class="info" style="left:177px;top:603px">(555) 010-4471<br>4200 Marlow Avenue Suite 310<br>Brenton, TX 75000</div>
<svg class="abs" style="left:410px;top:616px" width="12" height="12" viewBox="0 0 12 12"><path d="M2 0l2.5 3-1.3 1.5a7 7 0 0 0 4.3 4.3L9 7.5 12 10l-1.5 2C5 12 0 7 0 1.5z" fill="#3a2a10"/></svg>
<div class="info thin" style="left:431px;top:611px">(555) 018 362 907</div>
<svg class="abs" style="left:408px;top:651px" width="16" height="11" viewBox="0 0 16 11"><rect x=".5" y=".5" width="15" height="10" fill="none" stroke="#3a2a10"/><path d="M.5.5l7.5 6 7.5-6" fill="none" stroke="#3a2a10"/></svg>
<div class="info thin" style="left:431px;top:644px">hello@corvanthveylor.example</div>

<div class="map" role="img" aria-label="Street map showing the store location"></div>

<footer class="site-footer"></footer>
<h3 class="footer-heading" style="left:107px">INFORMATION</h3>
<h3 class="footer-heading" style="left:313px">MY ACCOUNT</h3>
<h3 class="footer-heading" style="left:509px">CONTACT US</h3>
<h3 class="footer-heading" style="left:962px">CONTACT US</h3>

<ul class="footer-list" style="left:107px;top:886px">
  <li>About Us</li><li>Contact Us</li><li>Return Policy</li><li>FAQ</li><li>Privacy Policy</li><li>Terms</li>
</ul>
<ul class="footer-list" style="left:313px;top:891px">
  <li>My Account</li><li>Return a item</li><li>My Wish List</li>
</ul>
<ul class="footer-list" style="left:511px;top:907px">
  <li>care@corvanthveylor.example</li><li>10:00 - 16:00, Monday - Friday</li>
</ul>
<ul class="footer-list" style="left:733px;top:907px">
  <li>Veylor Trading Ltd</li><li>27 Harrow Lane Unit 4C</li><li>State: Calder 10482</li><li>USA</li>
</ul>

<div class="social" style="left:960px" aria-label="Kestrel">K</div>
<div class="social" style="left:998px" aria-label="Pinly">P</div>
<div class="social" style="left:1035px" aria-label="Pictoval">Pv</div>
<div class="social" style="left:1071px" aria-label="Tumbra">T</div>

<p class="copyright">2018 Corvanthveylor.example All Rights Reserved.</p>

<div class="to-top">
  <svg width="42" height="42" viewBox="0 0 42 42"><path d="M21 31V11M13 19l8-8 8 8" fill="none" stroke="#fff" stroke-width="2"/></svg>
</div>

<div class="footer-bottom"></div>
<div class="currency">USD
  <svg width="12" height="8" viewBox="0 0 12 8" style="margin-left:4px"><path d="M1 7l5-5 5 5" fill="none" stroke="#ccc" stroke-width="1.3"/></svg>
</div>
<div class="divider"></div>
<div class="payments"><span>Payly</span><span>Cardo</span><span>Amvia</span><span>Sendra</span><span>Dinex</span><span>Findr</span></div>

</body>
</html>
```